Mobile app for checking bus arrival

I would like to make the UI much more beautiful and modern. The app is an app to check bus arrival in Singapore.
See here: https://apps.veltrano.com/store/apps/details?id=com.ridoka&hl=en

Based on the question from designers:

1. The first screen shows the favorite bus stop. Each item shows location / street, the top one is the location, second line is the street name. And the number is the bus stop code.

2. Please download the app and try bus stop code with 07589 or 10079, for example. It will bring you to the next screen.

3. The pencil allow you to select color theme, for the list item, and the header.

4. On the second screen, it will show up the list of bus route that available on that bus stop.

5. When you tap on one of them it will show you the 2 subsequent arrival time.

6. Each of the arrival time has the information of availability seats available, seats not available, no more space. (we can use green, yellow, red, respectively).

7. Each of the arrival time has the WAB indicator (Wheelchair availability). Show as icon is preferred.

7. KLT and VOPN are the bus provider in Singapore. 48 means the route /service no.

Requirements:
And check the attachment, see screen 3. I need to add information about the space availability, which has 3 state: seats available, seats not available, no more space. (we can use green, yellow, red, respectively).

Please advise how to show the information.

Target Market(s)

Students, age below 35

Industry/Entity Type

Trivex

Requirements
Must have
• The app currently has the capabilities to select color theme, checkout screen1. It's the button and the list item color.
Nice to have
• Please download the app to see all available colors, and make suggestion to have better color pallete.

```html
<!DOCTYPE html>
<html lang="en">
<head>
<meta charset="utf-8">
<title>Bus Arrival – My Favorite</title>
<link href="https://fonts.googleapis.com/css2?family=Roboto:wght@400;500&display=swap" rel="stylesheet">
<style>
  :root {
    --page-bg: #e4e4e4;
    --status-bar: #4a2a85;
    --app-bar: #673ab7;
    --map-band: #331b5e;
    --accent: #673ab7;
    --section-bg: #eff3f6;
    --row-bg: #ffffff;
    --divider: #e6e9ec;
    --title-text: #444444;
    --sub-text: #a9a9a9;
    --hint-text: #a0a0a0;
    --star: #f9a825;
    --white: #ffffff;
  }
  * { box-sizing: border-box; margin: 0; padding: 0; }
  html, body {
    width: 960px; height: 1200px; overflow: hidden;
    background: var(--page-bg);
    font-family: "Roboto", Arial, sans-serif;
  }
  .screen {
    position: absolute; left: 156px; top: 24px;
    width: 649px; height: 1152px;
    background: var(--row-bg);
    overflow: hidden;
  }
  .status-bar {
    height: 43px; background: var(--status-bar);
    display: flex; align-items: center; justify-content: flex-end;
    gap: 14px; padding-right: 17px; color: var(--white); font-size: 23px;
  }
  .app-bar {
    position: relative; height: 101px; background: var(--app-bar);
  }
  .menu-icon { position: absolute; left: 34px; top: 39px; }
  .search-box {
    position: absolute; left: 102px; top: 16px; width: 528px; height: 71px;
    background: var(--white); border-radius: 2px;
    display: flex; align-items: center; padding: 0 30px 0 32px;
    box-shadow: 0 1px 3px rgba(0,0,0,.2);
  }
  .search-box .hint { flex: 1; margin-left: 18px; font-size: 25px; color: var(--hint-text); }
  .map-band {
    height: 101px; background: var(--map-band);
    display: flex; align-items: center; justify-content: center;
    color: var(--white); font-size: 31px; letter-spacing: .3px;
  }
  .fab {
    position: absolute; left: 513px; top: 194px; width: 102px; height: 102px;
    border-radius: 50%; background: var(--accent);
    display: flex; align-items: center; justify-content: center;
    box-shadow: 0 4px 8px rgba(0,0,0,.3); z-index: 2;
  }
  .section-head {
    height: 107px; background: var(--section-bg);
    display: flex; align-items: center; padding-left: 32px;
    font-size: 39px; color: var(--title-text);
    border-bottom: 1px solid var(--divider);
  }
  .stop-list { list-style: none; }
  .stop-row {
    height: 120px; display: flex; align-items: center;
    padding-left: 33px; padding-right: 44px;
    border-bottom: 1px solid var(--divider);
  }
  .stop-code {
    width: 97px; height: 52px; background: var(--accent); color: var(--white);
    border-radius: 2px; display: flex; align-items: center; justify-content: center;
    font-size: 24px; letter-spacing: .5px;
  }
  .stop-info { flex: 1; margin-left: 22px; }
  .stop-name { font-size: 24px; color: var(--title-text); }
  .stop-street { font-size: 21px; color: var(--sub-text); margin-top: 8px; }
</style>
</head>
<body>
  <main class="screen">
    <div class="status-bar">
      <svg width="22" height="20" viewBox="0 0 22 20"><path d="M22 0V20H0Z" fill="rgba(255,255,255,.45)"/><path d="M14 8V20H2Z" fill="#fff"/></svg>
      <svg width="14" height="24" viewBox="0 0 14 24"><rect x="0" y="2" width="14" height="22" rx="1" fill="rgba(255,255,255,.45)"/><rect x="4" y="0" width="6" height="3" fill="rgba(255,255,255,.45)"/><rect x="0" y="12" width="14" height="12" rx="1" fill="#fff"/></svg>
      <span class="clock">12:30</span>
    </div>

    <header class="app-bar">
      <svg class="menu-icon" width="34" height="24" viewBox="0 0 34 24"><rect y="0" width="34" height="3" fill="#fff"/><rect y="10.5" width="34" height="3" fill="#fff"/><rect y="21" width="34" height="3" fill="#fff"/></svg>
      <div class="search-box">
        <svg width="32" height="32" viewBox="0 0 32 32"><circle cx="12.5" cy="12.5" r="9.5" fill="none" stroke="#9e9e9e" stroke-width="3"/><path d="M19.5 19.5L30 30" stroke="#9e9e9e" stroke-width="3.5" stroke-linecap="round"/></svg>
        <span class="hint">Bus Stop Code</span>
        <svg width="24" height="36" viewBox="0 0 24 36"><rect x="7" y="0" width="10" height="22" rx="5" fill="#9e9e9e"/><path d="M2 16a10 10 0 0 0 20 0" fill="none" stroke="#9e9e9e" stroke-width="2.5"/><rect x="10.8" y="26" width="2.4" height="9" fill="#9e9e9e"/></svg>
      </div>
    </header>

    <div class="map-band">Open Map</div>

    <div class="fab">
      <svg width="38" height="38" viewBox="0 0 24 24"><path d="M3 17.25V21h3.75L17.81 9.94l-3.75-3.75L3 17.25zM20.71 7.04a1 1 0 0 0 0-1.41l-2.34-2.34a1 1 0 0 0-1.41 0l-1.83 1.83 3.75 3.75 1.83-1.83z" fill="#fff"/></svg>
    </div>

    <h2 class="section-head" style="font-weight:400">My Favorite</h2>

    <ul class="stop-list">
      <li class="stop-row"><span class="stop-code">07589</span><div class="stop-info"><div class="stop-name">Opp Rochor Ctr</div><div class="stop-street">Ophir Rd</div></div><svg width="32" height="32" viewBox="0 0 24 24"><path d="M12 17.27L18.18 21l-1.64-7.03L22 9.24l-7.19-.61L12 2 9.19 8.63 2 9.24l5.46 4.73L5.82 21z" fill="var(--star)"/></svg></li>
      <li class="stop-row"><span class="stop-code">12119</span><div class="stop-info"><div class="stop-name">Police KINS Trg Camp</div><div class="stop-street">Ulu Pandan Rd</div></div><svg width="32" height="32" viewBox="0 0 24 24"><path d="M12 17.27L18.18 21l-1.64-7.03L22 9.24l-7.19-.61L12 2 9.19 8.63 2 9.24l5.46 4.73L5.82 21z" fill="var(--star)"/></svg></li>
      <li class="stop-row"><span class="stop-code">14009</span><div class="stop-info"><div class="stop-name">HarbourFront Int</div><div class="stop-street">Seah Im Rd</div></div><svg width="32" height="32" viewBox="0 0 24 24"><path d="M12 17.27L18.18 21l-1.64-7.03L22 9.24l-7.19-.61L12 2 9.19 8.63 2 9.24l5.46 4.73L5.82 21z" fill="var(--star)"/></svg></li>
      <li class="stop-row"><span class="stop-code">01012</span><div class="stop-info"><div class="stop-name">Hotel Serene Harbour</div><div class="stop-street">Victoria St</div></div><svg width="32" height="32" viewBox="0 0 24 24"><path d="M12 17.27L18.18 21l-1.64-7.03L22 9.24l-7.19-.61L12 2 9.19 8.63 2 9.24l5.46 4.73L5.82 21z" fill="var(--star)"/></svg></li>
      <li class="stop-row"><span class="stop-code">10659</span><div class="stop-info"><div class="stop-name">Blk 1003</div><div class="stop-street">Bt Merah Ctrl</div></div><svg width="32" height="32" viewBox="0 0 24 24"><path d="M12 17.27L18.18 21l-1.64-7.03L22 9.24l-7.19-.61L12 2 9.19 8.63 2 9.24l5.46 4.73L5.82 21z" fill="var(--star)"/></svg></li>
    </ul>
  </main>
</body>
</html>
```